Frostvale Harborline LLC

we need a business card design

Industry/Entity Type

hvac

Contact Information for Business Card

my logo

Requirements
Must have
• my logo and same colors

```html
<!DOCTYPE html>
<html lang="en">
<head>
<meta charset="utf-8">
<title>Frostvale Harborline LLC – Business Card</title>
<link rel="stylesheet" href="https://fonts.googleapis.com/css2?family=Montserrat:wght@400;500;700;800&display=swap">
<style>
  :root {
    --backdrop: #e9ecef;
    --card-blue: #1160a8;
    --sky-blue: #12aee0;
    --name-blue: #1ab0e6;
    --sun-orange: #f6b84a;
    --white: #ffffff;
  }
  * { margin: 0; padding: 0; box-sizing: border-box; }
  html, body {
    width: 1200px; height: 878px; overflow: hidden;
    background: var(--backdrop);
    font-family: "Montserrat", Arial, sans-serif;
  }
  .sheet {
    width: 1200px; height: 878px;
    display: flex; flex-direction: column; align-items: center; justify-content: center;
    gap: 30px;
  }
  .card {
    position: relative;
    width: 700px; height: 400px;
    background: var(--card-blue);
    overflow: hidden;
    box-shadow: 0 6px 18px rgba(0,0,0,0.18);
  }
  /* Back side */
  .card-back { display: flex; align-items: center; justify-content: center; }
  .brand-name {
    display: flex; align-items: center; gap: 12px;
    color: var(--white); font-weight: 800; letter-spacing: 0.5px;
    white-space: nowrap;
  }
  .brand-mark {
    width: 20px; height: 20px; border-radius: 50%;
    background: var(--sun-orange); flex: none;
  }
  .card-back .brand-name { font-size: 38px; }
  /* Front side */
  .card-waves { position: absolute; inset: 0; }
  .name-accent {
    position: absolute; left: 22px; top: 38px;
    width: 14px; height: 44px; background: var(--name-blue);
  }
  .holder { position: absolute; left: 50px; top: 36px; }
  .holder-name { font-size: 28px; font-weight: 800; letter-spacing: 0.5px; line-height: 1; }
  .holder-first { color: var(--name-blue); }
  .holder-last { color: var(--sun-orange); }
  .holder-role { color: var(--white); font-size: 18px; font-weight: 400; margin-top: 4px; }
  .address {
    position: absolute; left: 50px; top: 128px;
    color: var(--white); font-size: 18px; line-height: 1.4;
  }
  .contact-list {
    position: absolute; left: 40px; top: 198px;
    list-style: none; color: var(--white); font-size: 18px;
  }
  .contact-list li { display: flex; align-items: center; gap: 10px; height: 30px; }
  .contact-icon { width: 16px; height: 16px; flex: none; }
  .card-front .brand-name {
    position: absolute; right: 34px; top: 292px; font-size: 20px;
  }
  .card-front .brand-mark { width: 16px; height: 16px; }
</style>
</head>
<body>
<main class="sheet">
  <section class="card card-back" aria-label="Card back">
    <div class="brand-name"><span class="brand-mark"></span>Frostvale Harborline LLC</div>
  </section>

  <section class="card card-front" aria-label="Card front">
    <svg class="card-waves" viewBox="0 0 700 400" preserveAspectRatio="none" aria-hidden="true">
      <path d="M0,300 C110,350 260,365 430,362 C560,360 640,368 700,392 L700,400 L0,400 Z" fill="var(--sky-blue)"/>
      <path d="M0,288 C110,338 260,352 400,350" fill="none" stroke="var(--sun-orange)" stroke-width="9"/>
    </svg>

    <span class="name-accent"></span>
    <div class="holder">
      <div class="holder-name"><span class="holder-first">DELWYN</span> <span class="holder-last">MARSH</span></div>
      <div class="holder-role">Founder</div>
    </div>

    <p class="address">7/22 Quarry Hollow Rd<br>Brindlemere ABC 4410</p>

    <ul class="contact-list">
      <li>
        <svg class="contact-icon" viewBox="0 0 16 16" aria-hidden="true"><path d="M3 1l3 3-2 2c1 2 3 4 5 5l2-2 3 3-2 2C7 14 2 9 1 3z" fill="var(--sun-orange)"/></svg>
        555.214.0387
      </li>
      <li>
        <svg class="contact-icon" viewBox="0 0 16 16" aria-hidden="true"><rect x="1" y="3" width="14" height="10" fill="var(--sun-orange)"/><path d="M1 3l7 6 7-6" fill="none" stroke="var(--card-blue)" stroke-width="1.4"/></svg>
        info@frostvaleharbor.com
      </li>
      <li>
        <svg class="contact-icon" viewBox="0 0 16 16" aria-hidden="true"><g fill="none" stroke="var(--sun-orange)" stroke-width="1.4"><circle cx="8" cy="8" r="6.5"/><ellipse cx="8" cy="8" rx="3" ry="6.5"/><path d="M1.5 8h13M2.5 4.5h11M2.5 11.5h11"/></g></svg>
        www.frostvaleharbor.com
      </li>
    </ul>

    <div class="brand-name"><span class="brand-mark"></span>Frostvale Harborline LLC</div>
  </section>
</main>
</body>
</html>
```